Brightway Carpet and Tile cleaning Business card Design

I need a design that has the same feel as my van.
i would also like a prominent "Review us on facebook" somewhere, but not that it makes it look silly.
I would like the card to have a little bit of grey or black in the design as well.

It will need contact details
phone: 0455 817264
email: rkbrightwayclean@mailbox-example.com
website: www.brightwaycarpetandtilecleaning-example.com.au
facebook: /brightwaycarpetandtilecleaning

Industry/Entity Type

Business

Contact Information for Business Card

Phone number 0455817264
Email rkbrightwayclean@mailbox-example.com
Website www.brightwaycarpetandtilecleaning-example.com.au
Facebook/brightwaycarpetandtilecleaning

Colors
000000

Requirements
Must have
• Same feel as my van
• I want the card to stand out from the crowd
Nice to have
• Maybe include a tiny bit of a third colour? Grey's,blacks, orange?

```html
<!DOCTYPE html>
<html lang="en">
<head>
<meta charset="utf-8">
<title>Brightway Carpet and Tile Cleaning – Business Cards</title>
<link href="https://fonts.googleapis.com/css2?family=Open+Sans:wght@400;600;700;800&display=swap" rel="stylesheet">
<style>
  :root{
    --page:#eceeef;
    --card:#ffffff;
    --blue:#1a9fcf;
    --blue-deep:#0c7aa3;
    --blue-light:#bfe6f5;
    --green:#7cc242;
    --grey:#5e6468;
    --white:#ffffff;
  }
  *{margin:0;padding:0;box-sizing:border-box}
  html,body{width:1200px;height:900px;overflow:hidden;background:var(--page);font-family:"Open Sans",Arial,sans-serif}
  .stage{position:relative;width:1200px;height:900px}
  .card{position:absolute;background:var(--card);border-radius:18px;overflow:hidden;box-shadow:0 10px 30px rgba(0,0,0,.18)}
  .card--front{left:78px;top:35px;width:590px;height:365px}
  .card--back{left:390px;top:507px;width:565px;height:350px}
  .card svg.wave{position:absolute;inset:0;width:100%;height:100%}
  .brand{position:absolute;line-height:1}
  .brand__name{display:flex;align-items:center;gap:7px;font-weight:800;font-size:30px;color:var(--blue);letter-spacing:-.4px;white-space:nowrap}
  .brand__dot{width:11px;height:11px;border-radius:50%;background:var(--blue)}
  .brand__tag{margin-top:4px;margin-left:52px;font-weight:600;font-size:11px;letter-spacing:1.4px;color:var(--grey);white-space:nowrap}
  .card--front .brand{left:28px;top:98px}
  .card--back .brand{left:262px;top:100px}
  .contacts{position:absolute;right:38px;top:215px;list-style:none;text-align:right;color:var(--white);font-size:16.5px;font-weight:600}
  .contacts li{display:flex;justify-content:flex-end;align-items:center;gap:10px;height:29.5px;white-space:nowrap}
  .contacts svg{width:15px;height:15px;flex:none}
  .icon-square{width:14px;height:14px;background:var(--white);border-radius:2px;flex:none}
  .review{position:absolute;left:92px;top:274px;color:var(--white);font-weight:700;font-size:18px;letter-spacing:.2px;white-space:nowrap}
</style>
</head>
<body>
<main class="stage">

  <section class="card card--front" aria-label="Business card front">
    <svg class="wave" viewBox="0 0 590 365" preserveAspectRatio="none">
      <defs>
        <linearGradient id="frontBlue" x1="0" y1="0" x2="0" y2="1">
          <stop offset="0" stop-color="var(--blue-deep)"/>
          <stop offset="1" stop-color="var(--blue)"/>
        </linearGradient>
        <radialGradient id="frontSoft" cx=".55" cy=".25" r=".6">
          <stop offset="0" stop-color="var(--blue-light)" stop-opacity=".55"/>
          <stop offset="1" stop-color="var(--blue-light)" stop-opacity="0"/>
        </radialGradient>
      </defs>
      <rect width="590" height="230" fill="url(#frontSoft)" role="img" aria-label="Soft soap bubble pattern"/>
      <path d="M0,150 C110,245 240,265 360,190 S540,50 590,60 L590,365 L0,365Z" fill="var(--green)"/>
      <path d="M0,162 C110,257 240,277 362,202 S540,64 590,74 L590,365 L0,365Z" fill="var(--white)"/>
      <path d="M0,168 C110,263 240,283 364,208 S540,72 590,82 L590,365 L0,365Z" fill="url(#frontBlue)"/>
    </svg>

    <div class="brand">
      <div class="brand__name"><span class="brand__dot"></span>BrightwayClean</div>
      <div class="brand__tag">CARPET &amp; TILE CLEANING</div>
    </div>

    <ul class="contacts">
      <li>0455 817264
        <svg viewBox="0 0 24 24" aria-hidden="true"><path fill="#fff" d="M6.6 10.8a15.1 15.1 0 0 0 6.6 6.6l2.2-2.2a1 1 0 0 1 1-.25 11.4 11.4 0 0 0 3.6.57 1 1 0 0 1 1 1V20a1 1 0 0 1-1 1A17 17 0 0 1 3 4a1 1 0 0 1 1-1h3.5a1 1 0 0 1 1 1c0 1.25.2 2.45.57 3.6a1 1 0 0 1-.25 1z"/></svg></li>
      <li>rkbrightwayclean@mailbox-example.com
        <svg viewBox="0 0 24 24" aria-hidden="true"><rect x="2" y="5" width="20" height="14" rx="1" fill="#fff"/><path d="M3 6l9 7 9-7" fill="none" stroke="#1a9fcf" stroke-width="1.6"/></svg></li>
      <li>www.brightwaycarpetandtilecleaning-example.com.au
        <svg viewBox="0 0 24 24" aria-hidden="true"><circle cx="12" cy="12" r="10" fill="#fff"/><path d="M2 12h20M12 2c3 3 3 17 0 20M12 2c-3 3-3 17 0 20" fill="none" stroke="#1a9fcf" stroke-width="1.4"/></svg></li>
      <li>/brightwaycarpetandtilecleaning <span class="icon-square"></span></li>
    </ul>
  </section>

  <section class="card card--back" aria-label="Business card back">
    <svg class="wave" viewBox="0 0 565 350" preserveAspectRatio="none">
      <defs>
        <linearGradient id="backBlue" x1="0" y1="0" x2="0" y2="1">
          <stop offset="0" stop-color="var(--blue-deep)"/>
          <stop offset="1" stop-color="var(--blue)"/>
        </linearGradient>
        <radialGradient id="backSoft" cx=".25" cy=".2" r=".6">
          <stop offset="0" stop-color="var(--blue-light)" stop-opacity=".55"/>
          <stop offset="1" stop-color="var(--blue-light)" stop-opacity="0"/>
        </radialGradient>
      </defs>
      <rect width="565" height="200" fill="url(#backSoft)" role="img" aria-label="Soft soap bubble pattern"/>
      <path d="M0,110 C80,70 180,85 280,165 S470,290 565,160 L565,350 L0,350Z" fill="var(--green)"/>
      <path d="M0,122 C80,84 180,99 278,178 S470,304 565,175 L565,350 L0,350Z" fill="var(--white)"/>
      <path d="M0,128 C80,92 180,107 276,186 S470,312 565,183 L565,350 L0,350Z" fill="url(#backBlue)"/>
    </svg>

    <div class="brand">
      <div class="brand__name"><span class="brand__dot"></span>BrightwayClean</div>
      <div class="brand__tag">CARPET &amp; TILE CLEANING</div>
    </div>

    <p class="review">REVIEW US ON LINKSPACE</p>
  </section>

</main>
</body>
</html>
```